Clean business card with logo provided

I want a card that will stand out among the masses. I need the color and image to show professionalism and yet have a family appeal showing that I only deal with win/win scenarios. The back of the card will be used to take notes about the individual so I can use that in my database entry. I like modern design but need professionalism in it also. It needs to fit my "clean, safe, and affordable housing" motto. I need to be able to write on the file and update the card details for my employees.

Target Market(s)

Investors looking to make investment income through real estate

Industry/Entity Type

Real Estate

Contact Information for Business Card

Brent Kovalich
blank address, city, st, zip code
480-555-3174
brentkovalich@ridgeworthrentals.example
www.ridgeworthrentals.example

Font styles to use
Sans Serif

Requirements
Must have
• I would like the back of the card to have lines for info. example
• Met/Visited: Date:
• Interets:
Nice to have
• I want the cards color to match the logo background color. Font with details to be san serif and black. I want the card rectangular with square corners. Standard business card size. I would like to see cards designed with both images to see which i prefer more.

```html
<!DOCTYPE html>
<html lang="en">
<head>
<meta charset="utf-8">
<title>Ridgeworth Rentals – Business Card</title>
<link rel="stylesheet" href="https://fonts.googleapis.com/css2?family=Source+Sans+3:wght@400;600&display=swap">
<style>
  :root {
    --backdrop: #2c2c2c;
    --card-dark: #0c0c0c;
    --card-light: #ffffff;
    --teal: #1fa9c0;
    --text-light: #f2f2f2;
    --mark-tone: #e6e6e6;
    --rule: #222222;
  }
  * { margin: 0; padding: 0; box-sizing: border-box; }
  html, body {
    width: 1200px; height: 900px; overflow: hidden;
    background: var(--backdrop);
    font-family: "Source Sans 3", Arial, sans-serif;
  }
  .stage {
    position: relative; width: 1200px; height: 900px;
    display: flex; align-items: center; justify-content: center; gap: 40px;
  }
  .card {
    position: relative; width: 525px; height: 300px;
    border-radius: 24px; overflow: hidden;
  }
  /* Front */
  .card-front { background: var(--card-dark); color: var(--text-light); }
  .brand-figure {
    position: absolute; left: 40px; top: 75px; width: 150px; height: 150px;
    border-radius: 10px; background: var(--mark-tone);
  }
  .contact-block { position: absolute; left: 220px; top: 66px; right: 18px; }
  .person-name { color: var(--teal); font-size: 21px; font-weight: 600; margin-bottom: 12px; }
  .address { font-size: 13.5px; line-height: 1.25; margin-bottom: 18px; }
  .contact-list { list-style: none; font-size: 13.5px; }
  .contact-list li { display: flex; align-items: center; gap: 10px; margin-bottom: 6px; white-space: nowrap; }
  .contact-list svg { width: 12px; height: 12px; flex: none; fill: var(--teal); }
  /* Back */
  .card-back { background: var(--card-light); }
  .company-name {
    position: absolute; left: 44px; top: 46px;
    color: var(--teal); font-size: 34px; font-weight: 600; letter-spacing: 1px;
  }
  .tagline {
    position: absolute; left: 46px; top: 90px;
    color: var(--teal); font-size: 11px; font-weight: 400;
  }
  .note-fields { position: absolute; left: 44px; top: 150px; right: 40px; list-style: none; }
  .note-field { display: flex; align-items: flex-end; gap: 10px; margin-bottom: 16px; }
  .note-label { color: var(--teal); font-size: 17px; font-weight: 600; white-space: nowrap; }
  .note-line { flex: 1; border-bottom: 2px dotted var(--rule); margin-bottom: 5px; }
</style>
</head>
<body>
<main class="stage">
  <section class="card card-front" aria-label="Card front">
    <div class="brand-figure" role="img" aria-label="White manta ray illustration"></div>
    <div class="contact-block">
      <p class="person-name">Brent Kovalich</p>
      <p class="address">12345, Address Goes Here<br>Country Name, 123456</p>
      <ul class="contact-list">
        <li><svg viewBox="0 0 24 24" aria-hidden="true"><path d="M6.6 10.8a15.1 15.1 0 0 0 6.6 6.6l2.2-2.2c.3-.3.7-.4 1-.2 1.1.4 2.3.6 3.6.6.6 0 1 .4 1 1V20c0 .6-.4 1-1 1A17 17 0 0 1 3 4c0-.6.4-1 1-1h3.5c.6 0 1 .4 1 1 0 1.3.2 2.5.6 3.6.1.3 0 .7-.2 1z"/></svg>480-555-3174</li>
        <li><svg viewBox="0 0 24 24" aria-hidden="true"><path d="M2 5h20v14H2zM4 7v.4l8 5 8-5V7l-8 5z"/></svg>brentkovalich@ridgeworthrentals.example</li>
        <li><svg viewBox="0 0 24 24" aria-hidden="true"><circle cx="12" cy="12" r="10"/></svg>www.ridgeworthrentals.example</li>
      </ul>
    </div>
  </section>

  <section class="card card-back" aria-label="Card back">
    <p class="company-name">Ridgeworth Rentals</p>
    <p class="tagline">Providing clean, safe, and affordable housing</p>
    <ul class="note-fields">
      <li class="note-field"><span class="note-label">Visited Date:</span><span class="note-line"></span></li>
      <li class="note-field"><span class="note-label">Interets:</span><span class="note-line"></span></li>
      <li class="note-field"><span class="note-label">Problems:</span><span class="note-line"></span></li>
    </ul>
  </section>
</main>
</body>
</html>
```